Modern Business Card

Modern professional business card with more than just logo and demographic info. Something memorable.

We are a trendy/modern chiropractic group with an emphasis on neurology, hence the minimalist-type brain logo. We want to convey that modern and technical aspect with professionalism and the elite nature of our practice environment.

```html
<!DOCTYPE html>
<html lang="en">
<head>
<meta charset="utf-8">
<title>Axion Chiropractic — Business Card</title>
<link rel="stylesheet" href="https://fonts.googleapis.com/css2?family=Alegreya:wght@400;500&family=Saira+Semi+Condensed:wght@500&family=Roboto:wght@400&display=swap">
<style>
  :root {
    --backdrop: #bcbcbc;
    --card: #f1f1f0;
    --brand-blue: #3f63a0;
    --brand-dark: #3b2e33;
    --ink: #1c1a1b;
    --on-blue: #eef2f9;
    --shadow: rgba(0, 0, 0, 0.28);
  }
  * { box-sizing: border-box; margin: 0; padding: 0; }
  html, body {
    width: 1200px; height: 576px; overflow: hidden;
    background: var(--backdrop);
  }
  .canvas { position: relative; width: 1200px; height: 576px; }

  .card {
    position: absolute;
    background: var(--card);
    border-radius: 8px;
    overflow: hidden;
    box-shadow: 0 3px 6px var(--shadow);
  }

  /* Front */
  .card--front { left: 82px; top: 139px; width: 484px; height: 293px; }
  .front-brand {
    position: absolute; left: 0; right: 0; top: 100px;
    display: flex; align-items: center; justify-content: center; gap: 14px;
  }
  .brand-dot {
    width: 46px; height: 46px; border-radius: 50%;
    background: var(--brand-blue);
  }
  .brand-name {
    font-family: "Alegreya", serif; font-weight: 500;
    color: var(--ink); line-height: 0.95; text-align: left;
  }
  .front-brand .brand-name { font-size: 34px; }
  .brand-name span { display: block; }
  .front-web {
    position: absolute; left: 0; right: 0; top: 245px;
    display: flex; align-items: center; justify-content: center; gap: 14px;
    font-family: "Roboto", sans-serif; font-size: 12.5px; color: var(--ink);
  }
  .front-web svg { display: block; }
  .front-bands {
    position: absolute; left: 0; right: 0; bottom: 0; height: 12px; display: flex;
  }
  .front-bands .band--blue { flex: 1; background: var(--brand-blue); }
  .front-bands .band--dark { flex: 1; background: var(--brand-dark); }

  /* Back */
  .card--back { left: 602px; top: 138px; width: 481px; height: 291px; }
  .back-shape { position: absolute; inset: 0; }
  .person {
    position: absolute; left: 23px; top: 27px; color: var(--on-blue);
  }
  .person-name {
    font-family: "Saira Semi Condensed", sans-serif; font-weight: 500;
    font-size: 18px; line-height: 1.2;
  }
  .person-role {
    font-family: "Alegreya", serif; font-size: 12.5px; margin-top: 2px;
  }
  .contact {
    position: absolute; left: 23px; top: 167px;
    list-style: none; color: var(--on-blue);
    font-family: "Alegreya", serif; font-size: 12.5px; line-height: 18px;
  }
  .contact li { display: flex; align-items: center; gap: 8px; }
  .contact svg { width: 10px; height: 10px; flex: none; }
  .address {
    position: absolute; left: 23px; top: 226px; font-style: normal;
    color: var(--on-blue); font-family: "Alegreya", serif;
    font-size: 12.5px; line-height: 18px;
  }
  .back-brand {
    position: absolute; left: 258px; right: 0; top: 72px;
    display: flex; flex-direction: column; align-items: center; gap: 14px;
  }
  .back-brand .brand-name { font-size: 30px; text-align: center; }
</style>
</head>
<body>
<main class="canvas">

  <section class="card card--front" aria-label="Card front">
    <div class="front-brand">
      <div class="brand-dot"></div>
      <div class="brand-name"><span>AXION</span><span>CHIROPRACTIC</span></div>
    </div>
    <div class="front-web">
      <svg width="46" height="4" viewBox="0 0 46 4"><path d="M0 2 L46 0.5 L46 3.5 Z" fill="var(--brand-blue)"/></svg>
      <span>www.axionchiro.com</span>
      <svg width="46" height="4" viewBox="0 0 46 4"><path d="M46 2 L0 0.5 L0 3.5 Z" fill="var(--brand-blue)"/></svg>
    </div>
    <div class="front-bands"><div class="band--blue"></div><div class="band--dark"></div></div>
  </section>

  <section class="card card--back" aria-label="Card back">
    <svg class="back-shape" width="481" height="291" viewBox="0 0 481 291">
      <path d="M0 0 H285 Q214 145 281 291 H0 Z" fill="var(--brand-dark)"/>
      <path d="M0 0 H278 Q207 145 274 291 H0 Z" fill="var(--brand-blue)"/>
    </svg>
    <div class="person">
      <p class="person-name">Daniel Reyes Hart</p>
      <p class="person-role">Managing Director</p>
    </div>
    <ul class="contact">
      <li><svg viewBox="0 0 10 10"><path d="M1 3 Q1 1 3 1 H7 Q9 1 9 3 V4 H7 V3 H3 V4 H1 Z M2 5 H8 L9 9 H1 Z" fill="var(--on-blue)"/></svg>555-010-0142</li>
      <li><svg viewBox="0 0 10 10"><rect x="0.5" y="2" width="9" height="6.5" fill="none" stroke="var(--on-blue)"/><path d="M0.5 2 L5 5.5 L9.5 2" fill="none" stroke="var(--on-blue)"/></svg>daniel@axionchiro.com</li>
      <li><svg viewBox="0 0 10 10"><circle cx="5" cy="5" r="4.3" fill="none" stroke="var(--on-blue)"/><ellipse cx="5" cy="5" rx="1.8" ry="4.3" fill="none" stroke="var(--on-blue)"/><path d="M0.7 5 H9.3" stroke="var(--on-blue)"/></svg>www.axionchiro.com</li>
    </ul>
    <address class="address">81 Linden Row, Maple Falls,<br>WA 98266</address>
    <div class="back-brand">
      <div class="brand-dot"></div>
      <div class="brand-name"><span>AXION</span><span>CHIROPRACTIC</span></div>
    </div>
  </section>

</main>
</body>
</html>
```